Buch-/eBook-Cover für einen Elternratgeber
Zielgruppe
Buch: Elternratgeber
Titel: Werte lernen
Untertitel: Deinem Kind den richtigen Umgang beibringen
Wir sind der BRAM Verlag und suchen ein passendes Cover für unseren neuen Elternratgeber. Mit diesem Buch möchten wir Eltern unterstützen, ihren Kindern einen guten und verantwortungsvollen Umgang mit Geld zu vermitteln.
Anforderungen an das Cover-Design:
Bitte keinen Comicstil
Das Buch richtet sich an Eltern (nicht kindlich oder verspielt gestalten)
Keine direkte Darstellung von Geld (z. B. keine Münzen, Geldscheine, Sparschweine usw.)
Ob mit oder ohne Personen auf dem Cover: sind wir offen
Farbwahl und Bildsprache: gerne seriös, ansprechend und modern
Wir sind gespannt auf kreative und professionelle Vorschläge!
E-Book E-Book"
Das Design darf nicht zu überladen sein.

```html
<!DOCTYPE html>
<html lang="de">
<head>
<meta charset="utf-8">
<title>Werte lernen – BRAM Verlag</title>
<link rel="stylesheet" href="https://fonts.googleapis.com/css2?family=Source+Serif+4:opsz,wght@8..60,400;8..60,600;8..60,700&display=swap">
<style>
  :root {
    --backdrop: #76a078;
    --paper: #e5d6bc;
    --ink: #2c4150;
    --art-light: #ddd0b2;
    --art-mid: #b7b48a;
    --art-dark: #8e9066;
  }
  * { margin: 0; padding: 0; box-sizing: border-box; }
  html, body {
    width: 1200px;
    height: 1200px;
    overflow: hidden;
    background: var(--backdrop);
  }
  .cover {
    position: absolute;
    left: 250px;
    top: 45px;
    width: 700px;
    height: 1110px;
    background: var(--paper);
    font-family: "Source Serif 4", Georgia, serif;
    color: var(--ink);
  }
  .frame {
    position: absolute;
    left: 30px;
    top: 43px;
    width: 641px;
    height: 1035px;
    border: 2.5px solid var(--ink);
  }
  .label {
    position: absolute;
    left: 50%;
    transform: translateX(-50%);
    background: var(--ink);
    color: var(--paper);
    display: flex;
    align-items: center;
    justify-content: center;
    text-transform: uppercase;
    white-space: nowrap;
  }
  .label--genre {
    top: 16px;
    width: 245px;
    height: 38px;
    font-size: 20px;
    font-weight: 400;
    letter-spacing: 0.5px;
  }
  .label--publisher {
    top: 1055px;
    width: 223px;
    height: 42px;
    font-size: 25px;
    font-weight: 700;
  }
  .title {
    position: absolute;
    left: 0;
    width: 100%;
    top: 120px;
    text-align: center;
    font-weight: 700;
    line-height: 1;
  }
  .title__main {
    display: block;
    font-size: 168px;
    letter-spacing: -1px;
  }
  .title__sub {
    display: block;
    font-size: 118px;
    margin-top: -4px;
  }
  .rule {
    position: absolute;
    left: 88px;
    top: 412px;
    width: 534px;
    height: 2.5px;
    background: var(--ink);
  }
  .subtitle {
    position: absolute;
    left: 0;
    width: 100%;
    top: 440px;
    text-align: center;
    font-size: 32px;
    font-weight: 400;
    line-height: 1.15;
    letter-spacing: 0.3px;
  }
  .artwork {
    position: absolute;
    left: 90px;
    top: 620px;
    width: 532px;
    height: 323px;
    background: radial-gradient(ellipse at 50% 60%, var(--art-mid) 0%, var(--art-dark) 35%, var(--art-light) 72%, var(--paper) 100%);
    border-radius: 8px;
  }
</style>
</head>
<body>
  <main class="cover">
    <div class="frame"></div>
    <div class="label label--genre">Elternratgeber</div>

    <h1 class="title">
      <span class="title__main">Werte</span>
      <span class="title__sub">lernen</span>
    </h1>

    <div class="rule"></div>

    <p class="subtitle">Deinem Kind den richtigen<br>Umgang beibringen</p>

    <div class="artwork" role="img" aria-label="Illustration: ein aus Papier gefaltetes Schiffchen in gedämpftem Olivgrün auf hellem Grund"></div>

    <div class="label label--publisher">BRAM Verlag</div>
  </main>
</body>
</html>
```